Ridge Lass Crew (Flyer)

I want a flyer to advertise my service.
Details below, and logo's to use are attached.

A girls only after school program, 11-14yrs, as OSHC is no longer avail, dedicated to coaching & mentoring our girls into strong, independent young women.

The Brainchild of Rebecca Folwin, Ridge Lass Crew was created to address the growing demand for after school/school holiday supervision for kids moving from primary into high school, when OSHC ceases to exist.
With over 12 years experience mentoring and coaching young women in the corporate world, Bec decided to leave her role as a Director with Tarrant Trust, and follow her passion.
Bec, along with her sister Lorraine, who has over 10 years experience in local communities as a Youth Worker, and is also a qualified Enrolled Nurse, embarked on building a program designed to keep parents happy (by knowing their girls are safe) and dedicated to coaching and mentoring our girls into strong, independent young women.
Open every afternoon and during school holidays, we look to offer;
- Daily meditation
- Healthy snacks
- Dedicated homework time
- Organised group activity, led by qualified instructors (yoga, fitness class, soccer etc)
- Regular guests speakers, addressing issues/concerns for young people today
- SOCIAL MEDIA FREE ZONE

Located 87 Pelham Pde, Kestrel Heights (across from Crestmoor Day Clinic)
Open 3-6pm Monday to Friday

Facebook page: http://fb.example/ridgelasscrew
Email: info@ridgelasscrew.example.au
Mobile: 0455817396

Target Market(s)

Parents of teenage girls, teenage girls 11-14 years

Industry/Entity Type

School

Font styles to use
Sans Serif

Colors
b768aa
e667a6

Requirements
Must have
• What progam is - see brief
• Who runs it
Should not have
• Not be too busy, not overly mature images

```html
<!DOCTYPE html>
<html lang="en">
<head>
<meta charset="utf-8">
<title>Ridge Lass Crew – After School Program Flyer</title>
<link rel="stylesheet" href="https://fonts.googleapis.com/css2?family=Cinzel:wght@500;600&family=Quattrocento:wght@700&family=Open+Sans:wght@700;800&family=Caveat:wght@600&family=Lora:ital,wght@1,500&family=Cabin:wght@700&family=Roboto+Condensed:wght@300;400&display=swap">
<style>
  :root {
    --purple: #b768aa;
    --purple-deep: #8f4f86;
    --pink: #e667a6;
    --pink-band: #d36aa6;
    --white: #ffffff;
    --ink: #231a24;
    --soft-ink: #3a3340;
    --photo-light: #e9e6e8;
    --photo-mid: #c9bfc6;
  }
  * { margin: 0; padding: 0; box-sizing: border-box; }
  html, body { width: 848px; height: 1200px; overflow: hidden; background: var(--white); }
  .flyer {
    position: relative; width: 848px; height: 1200px; overflow: hidden;
    background: var(--purple);
    font-family: "Open Sans", sans-serif;
  }
  .flyer-shapes { position: absolute; inset: 0; }

  .logo-box {
    position: absolute; left: 24px; top: 14px; width: 258px; height: 309px;
    background: var(--white);
    display: flex; align-items: center; justify-content: center; text-align: center;
  }
  .logo-name {
    font-family: "Quattrocento", serif; font-weight: 700;
    font-size: 46px; line-height: 1.05; color: var(--pink);
  }

  .headline-bar {
    position: absolute; right: 342px; background: var(--pink-band);
    color: var(--white); font-family: "Quattrocento", serif; font-weight: 700;
    text-align: right; padding-right: 14px; white-space: nowrap;
  }
  .headline-bar.line-1 { left: 118px; top: 346px; height: 56px; font-size: 38px; line-height: 56px; }
  .headline-bar.line-2 { left: 166px; top: 406px; height: 55px; font-size: 38px; line-height: 55px; }
  .headline-bar.line-3 {
    left: 190px; top: 465px; height: 54px; line-height: 54px;
    font-family: "Open Sans", sans-serif; font-size: 30px;
  }
  .headline-bar.line-3 .age { font-size: 40px; font-weight: 800; }
  .headline-note {
    position: absolute; right: 362px; top: 526px;
    color: var(--white); font-size: 20px; font-weight: 700; white-space: nowrap;
  }

  .founder-line {
    position: absolute; left: 20px; top: 694px;
    font-family: "Cinzel", serif; font-weight: 600; font-size: 25px; color: var(--ink);
    letter-spacing: 0.5px; white-space: nowrap;
  }
  .program-name {
    position: absolute; left: 82px; top: 754px;
    font-family: "Cinzel", serif; font-weight: 500; font-size: 41px; color: var(--ink);
    letter-spacing: 1.5px; white-space: nowrap;
  }

  .hours {
    position: absolute; left: 560px; top: 728px;
    font-family: "Caveat", cursive; font-weight: 600; font-size: 31px; color: var(--ink);
    white-space: nowrap;
  }
  .open-note {
    position: absolute; left: 536px; top: 788px; width: 290px; text-align: center;
    font-size: 22px; font-weight: 700; line-height: 42px; color: var(--purple);
  }

  .offer-title {
    position: absolute; left: 18px; top: 892px;
    font-family: "Cabin", sans-serif; font-weight: 700; font-size: 31px; color: #f6eef4;
  }
  .offer-list { position: absolute; left: 18px; top: 948px; list-style: none; }
  .offer-item {
    position: relative; padding-left: 26px;
    font-family: "Lora", serif; font-style: italic; font-weight: 500;
    font-size: 22px; line-height: 26px; color: var(--white);
  }
  .offer-item + .offer-item { margin-top: 9px; }
  .offer-item.spaced { margin-top: 16px; }
  .offer-item svg { position: absolute; left: 0; top: 4px; }
  .offer-item .sub { display: block; padding-left: 2px; }

  .contact { position: absolute; right: 72px; text-align: right; font-family: "Roboto Condensed", sans-serif; color: var(--ink); }
  .contact-label { font-size: 21px; font-weight: 300; }
  .contact-value { font-size: 18px; font-weight: 400; }
  .contact .phone-number { color: var(--pink); font-size: 19px; letter-spacing: 0.5px; }
  .contact-icon { position: absolute; right: -40px; }
  .contact.call { top: 922px; }
  .contact.mail { top: 1010px; }
  .contact.social { top: 1074px; }
  .contact.address { top: 1126px; line-height: 24px; }
  .address-note { position: absolute; right: 65px; top: 1178px; font-family: "Roboto Condensed", sans-serif; font-size: 13px; color: var(--ink); }
</style>
</head>
<body>
<main class="flyer">
  <svg class="flyer-shapes" width="848" height="1200" viewBox="0 0 848 1200">
    <defs>
      <linearGradient id="shirtTone" x1="0" y1="0" x2="1" y2="1">
        <stop offset="0" stop-color="var(--photo-mid)"/>
        <stop offset="0.45" stop-color="var(--photo-light)"/>
        <stop offset="1" stop-color="#d8cdd4"/>
      </linearGradient>
    </defs>
    <polygon points="60,0 848,0 848,304 584,668" fill="url(#shirtTone)" role="img" aria-label="Photo of a girl wearing a white program t-shirt"/>
    <polygon points="0,670 584,670 540,742 440,850 0,850" fill="var(--pink-band)"/>
    <polygon points="584,672 848,304 848,1200 572,1200 400,952" fill="var(--white)"/>
    <polygon points="400,952 430,996 572,1200 540,1200 418,1024" fill="var(--purple-deep)"/>
    <polygon points="584,672 600,700 430,952 400,952" fill="var(--purple-deep)" opacity="0.55"/>
  </svg>

  <div class="logo-box"><span class="logo-name">Ridge Lass<br>Crew</span></div>

  <div class="headline-bar line-1">A Girls Only After</div>
  <div class="headline-bar line-2">School Program</div>
  <div class="headline-bar line-3">For <span class="age">11-14yrs</span></div>
  <p class="headline-note">as OSHC is no longer available</p>

  <p class="founder-line">The Brainchild of Rebecca Folwin</p>
  <h1 class="program-name">Ridge Lass Crew</h1>

  <p class="hours">3-6pm Monday to Friday</p>
  <p class="open-note">Open every afternoon &amp;<br>during school holidays</p>

  <h2 class="offer-title">We look to offer</h2>
  <ul class="offer-list">
    <li class="offer-item"><svg width="16" height="16" viewBox="0 0 16 16"><circle cx="8" cy="8" r="6.5" fill="none" stroke="#fff" stroke-width="1.6"/><path d="M5 8.2l2 2 4-4" fill="none" stroke="#fff" stroke-width="1.6"/></svg>Daily meditation</li>
    <li class="offer-item"><svg width="16" height="16" viewBox="0 0 16 16"><circle cx="8" cy="8" r="6.5" fill="none" stroke="#fff" stroke-width="1.6"/><path d="M5 8.2l2 2 4-4" fill="none" stroke="#fff" stroke-width="1.6"/></svg>Healthy snacks</li>
    <li class="offer-item"><svg width="16" height="16" viewBox="0 0 16 16"><circle cx="8" cy="8" r="6.5" fill="none" stroke="#fff" stroke-width="1.6"/><path d="M5 8.2l2 2 4-4" fill="none" stroke="#fff" stroke-width="1.6"/></svg>Organised group activity,<span class="sub">(yoga, fitness class, soccer etc.)</span></li>
    <li class="offer-item"><svg width="16" height="16" viewBox="0 0 16 16"><circle cx="8" cy="8" r="6.5" fill="none" stroke="#fff" stroke-width="1.6"/><path d="M5 8.2l2 2 4-4" fill="none" stroke="#fff" stroke-width="1.6"/></svg>Regular guests speakers</li>
    <li class="offer-item spaced"><svg width="16" height="16" viewBox="0 0 16 16"><circle cx="8" cy="8" r="6.5" fill="none" stroke="#fff" stroke-width="1.6"/><path d="M5 8.2l2 2 4-4" fill="none" stroke="#fff" stroke-width="1.6"/></svg>Dedicated homework time</li>
    <li class="offer-item spaced"><svg width="16" height="16" viewBox="0 0 16 16"><circle cx="8" cy="8" r="6.5" fill="none" stroke="#fff" stroke-width="1.6"/><path d="M5 8.2l2 2 4-4" fill="none" stroke="#fff" stroke-width="1.6"/></svg>Social media free zone</li>
  </ul>

  <div class="contact call">
    <div class="contact-label">Call Us Now</div>
    <div class="contact-value phone-number">0455817396</div>
    <svg class="contact-icon" style="top:8px" width="24" height="30" viewBox="0 0 24 30"><path d="M6 3l4 6-3 2c1 4 4 8 7 10l2-3 5 4-2 4c-8-1-16-11-16-19z" fill="none" stroke="var(--soft-ink)" stroke-width="1.4"/></svg>
  </div>
  <div class="contact mail">
    <div class="contact-label">e-Mail us</div>
    <div class="contact-value">info@ridgelasscrew.example.au</div>
    <svg class="contact-icon" style="top:4px" width="24" height="26" viewBox="0 0 24 26"><rect x="1" y="8" width="22" height="16" fill="none" stroke="var(--soft-ink)" stroke-width="1.4"/><path d="M1 8l11 9 11-9M1 24l8-8M23 24l-8-8M1 8l11-7 11 7" fill="none" stroke="var(--soft-ink)" stroke-width="1.4"/></svg>
  </div>
  <div class="contact social">
    <div class="contact-value">http://fb.example/ridgelasscrew</div>
    <svg class="contact-icon" style="top:1px" width="20" height="20" viewBox="0 0 20 20"><rect x="1" y="1" width="18" height="18" rx="3" fill="#4a69b0"/></svg>
  </div>
  <div class="contact address">
    <div class="contact-value">87 Pelham Pde,<br>Kestrel Heights</div>
    <svg class="contact-icon" style="top:10px" width="24" height="28" viewBox="0 0 24 28"><circle cx="11" cy="14" r="9" fill="none" stroke="var(--soft-ink)" stroke-width="1.3"/><ellipse cx="11" cy="14" rx="4" ry="9" fill="none" stroke="var(--soft-ink)" stroke-width="1.1"/><path d="M2 14h18M4 9h14M4 19h14" stroke="var(--soft-ink)" stroke-width="1.1"/><path d="M18 2a4 4 0 0 1 4 4c0 3-4 7-4 7s-4-4-4-7a4 4 0 0 1 4-4z" fill="var(--white)" stroke="var(--soft-ink)" stroke-width="1.2"/></svg>
  </div>
  <p class="address-note">(across from Crestmoor Day Clinic)</p>
</main>
</body>
</html>
```